Harborview Optical -Window Poster (Optometrist)

We are an optometry practice and we need a poster for a new store promotion for our window highlighting we now also sell 2 pairs of glasses as a package deal. The size will be 1300mm width x 1900mm height

The artwork will be displayed as a fabric banner in our shop window. We have 7 other banners with different services our business provides. The words needs to standout for passers by and the cars stopped at the traffic lights out front of our business. We already have signs with our logos phone number etc. so we won't need them included in the poster.

It would need to include the following information.

Two pair packages now available*

*Conditions apply

The artwork will be displayed as a fabric banner in our shop window. We have 7 other banners with different services our business provides. The words needs to standout for passers by and the cars stopped at the traffic lights out front of our business. We already have signs with our logos phone number etc. so we won't need them included in the poster. Thank you for your work it's amazing Added Saturday, February 18, 2017

The artwork will be displayed as a fabric banner in our shop window. We have 7 other banners with different services our business provides. The words needs to standout for passers by and the cars stopped at the traffic lights out front of our business. We already have signs with our logos phone number etc. so we won't need them included in the poster. Added Saturday, February 18, 2017

Target Market(s)

Cars driving past and stopped at traffic lights outside our store.

Industry/Entity Type

Optician

Requirements
Must have
• Poster must say:
• Two pair packages now available*
• *Conditions apply

```html
<!DOCTYPE html>
<html lang="en">
<head>
<meta charset="utf-8">
<title>Harborview Optical – Two Pair Packages Window Poster</title>
<link rel="stylesheet" href="https://fonts.googleapis.com/css2?family=Bebas+Neue&family=Josefin+Sans:wght@600&display=swap">
<style>
  :root {
    --poster-black: #060606;
    --headline-white: #f4f2ee;
    --alert-red: #ee1c25;
    --package-orange: #f0961e;
    --terms-yellow: #fff200;
    --retina-deep: #4a1812;
    --retina-mid: #6a2a22;
    --retina-glow: #8a4a2a;
    --streak-blue: rgba(120, 150, 190, 0.35);
  }
  html, body {
    margin: 0;
    padding: 0;
    width: 962px;
    height: 1200px;
    overflow: hidden;
    background: var(--poster-black);
  }
  .poster {
    position: relative;
    width: 962px;
    height: 1200px;
    background: var(--poster-black);
    overflow: hidden;
  }
  .poster__decor {
    position: absolute;
    inset: 0;
  }
  .headline-tag {
    position: absolute;
    top: 78px;
    right: 28px;
    margin: 0;
    font-family: "Bebas Neue", "Oswald", sans-serif;
    font-size: 80px;
    line-height: 1;
    letter-spacing: 3px;
    color: var(--alert-red);
  }
  .headline {
    position: absolute;
    left: 0;
    right: 0;
    top: 398px;
    margin: 0;
    text-align: center;
  }
  .headline__main {
    display: block;
    font-family: "Bebas Neue", "Oswald", sans-serif;
    font-weight: 400;
    font-size: 196px;
    line-height: 1;
    letter-spacing: 8px;
    color: var(--headline-white);
    text-shadow: 6px 7px 0 #000;
    padding-left: 10px;
  }
  .headline__sub {
    display: block;
    margin-top: 8px;
    font-family: "Josefin Sans", "Century Gothic", sans-serif;
    font-weight: 600;
    font-size: 92px;
    line-height: 1;
    letter-spacing: 2px;
    color: var(--package-orange);
    padding-left: 12px;
  }
  .terms {
    position: absolute;
    left: 0;
    right: 0;
    top: 1036px;
    margin: 0;
    text-align: center;
    font-family: "Bebas Neue", "Oswald", sans-serif;
    font-size: 62px;
    line-height: 1;
    letter-spacing: 6px;
    color: var(--terms-yellow);
  }
</style>
</head>
<body>
  <main class="poster">
    <svg class="poster__decor" width="962" height="1200" viewBox="0 0 962 1200" aria-hidden="false">
      <defs>
        <radialGradient id="retinaFill" cx="0.22" cy="0.45" r="0.85">
          <stop offset="0" stop-color="var(--retina-glow)"/>
          <stop offset="0.25" stop-color="var(--retina-mid)"/>
          <stop offset="1" stop-color="var(--retina-deep)"/>
        </radialGradient>
        <linearGradient id="streakLeft" x1="0" x2="1">
          <stop offset="0" stop-color="var(--streak-blue)"/>
          <stop offset="1" stop-color="rgba(120,150,190,0)"/>
        </linearGradient>
        <linearGradient id="streakRight" x1="1" x2="0">
          <stop offset="0" stop-color="var(--streak-blue)"/>
          <stop offset="1" stop-color="rgba(120,150,190,0)"/>
        </linearGradient>
        <linearGradient id="underline" x1="0" x2="1">
          <stop offset="0" stop-color="rgba(255,255,255,0)"/>
          <stop offset="0.5" stop-color="#ffffff"/>
          <stop offset="1" stop-color="rgba(255,255,255,0)"/>
        </linearGradient>
        <radialGradient id="flare">
          <stop offset="0" stop-color="rgba(220,225,235,0.6)"/>
          <stop offset="1" stop-color="rgba(220,225,235,0)"/>
        </radialGradient>
      </defs>

      <rect class="streak" x="0" y="52" width="360" height="4" fill="url(#streakLeft)"/>
      <rect class="streak" x="500" y="170" width="462" height="5" fill="url(#streakRight)"/>
      <rect class="streak" x="0" y="1008" width="480" height="5" fill="url(#streakLeft)"/>

      <ellipse class="flare" cx="45" cy="180" rx="45" ry="22" fill="url(#flare)"/>
      <ellipse class="flare" cx="895" cy="375" rx="50" ry="24" fill="url(#flare)"/>

      <ellipse class="retina-photo" role="img" aria-label="Photograph of a retina with branching blood vessels"
               cx="480" cy="576" rx="462" ry="394" fill="url(#retinaFill)"/>

      <rect class="terms-underline" x="348" y="1101" width="314" height="3" fill="url(#underline)"/>
    </svg>

    <p class="headline-tag">Now Available*</p>

    <h1 class="headline">
      <span class="headline__main">TWO PAIR</span>
      <span class="headline__sub">PACKAGES</span>
    </h1>

    <p class="terms">*Conditions Apply</p>
  </main>
</body>
</html>
```